Veldmark Supplies Business Card

Professional business card that stand out to our potential customers. Front and back with clean modern design

Industry/Entity Type

Oil and gas

Contact Information for Business Card

Name, address, website , office phone and cell number

Requirements
Must have
• Editable files for each employee

```html
<!DOCTYPE html>
<html lang="en">
<head>
<meta charset="utf-8">
<title>Veldmark Supplies – Business Card</title>
<link rel="stylesheet" href="https://fonts.googleapis.com/css2?family=Poppins:wght@300;400;500;600;700&display=swap">
<style>
  :root {
    --backdrop: #dfe3e5;
    --card-dark: #222226;
    --card-dark-raised: #2a2a2f;
    --paper: #ffffff;
    --brand-red: #e8262a;
    --brand-blue: #14b2d6;
    --ink-light: #f2f2f2;
  }
  * { box-sizing: border-box; margin: 0; padding: 0; }
  html, body { width: 1200px; height: 960px; overflow: hidden; }
  body {
    background: var(--backdrop);
    font-family: "Poppins", sans-serif;
    position: relative;
  }
  .card {
    position: absolute;
    top: 105px;
    width: 429px;
    height: 750px;
    border-radius: 34px;
    overflow: hidden;
    background: var(--card-dark);
  }
  .card--back { left: 141px; }
  .card--front { left: 629px; }

  /* Back side */
  .back-mark {
    position: absolute;
    left: 0; right: 0; top: 345px;
    text-align: center;
    font-size: 30px;
    font-weight: 600;
    letter-spacing: 2px;
    color: var(--card-dark-raised);
    text-transform: uppercase;
  }

  /* Front side */
  .front-top {
    position: absolute;
    left: 0; top: 0;
    width: 100%;
    height: 243px;
    background: var(--paper);
  }
  .brand-line {
    position: absolute;
    left: 0; right: 0; top: 40px;
    text-align: center;
    font-size: 24px;
    font-weight: 700;
    letter-spacing: 1px;
    color: var(--brand-red);
    text-transform: uppercase;
  }
  .brand-dot {
    position: absolute;
    left: 174px; top: 173px;
    width: 80px; height: 80px;
    border-radius: 50%;
    background: var(--brand-red);
  }
  .brand-name-mid {
    position: absolute;
    left: 0; right: 0; top: 272px;
    text-align: center;
    font-size: 22px;
    font-weight: 600;
    color: var(--brand-red);
  }
  .person-name {
    position: absolute;
    left: 0; right: 0; top: 383px;
    text-align: center;
    font-size: 35px;
    line-height: 1.2;
  }
  .person-name .first { color: var(--brand-red); font-weight: 600; }
  .person-name .last { color: var(--brand-blue); font-weight: 400; }
  .person-role {
    position: absolute;
    left: 0; right: 0; top: 430px;
    text-align: center;
    font-size: 19px;
    font-weight: 500;
    color: var(--ink-light);
  }
  .dot-row {
    position: absolute;
    left: 0;
    width: 429px;
    height: 34px;
  }
  .dot-row--contact { top: 464px; }
  .dot-row--address { top: 625px; }
  .dot-row circle.dot, .dot-row circle.badge { fill: var(--brand-red); }
  .dot-row .glyph { fill: none; stroke: var(--paper); stroke-width: 1.5; stroke-linecap: round; stroke-linejoin: round; }
  .contact-list, .address {
    position: absolute;
    left: 0; right: 0;
    text-align: center;
    color: var(--ink-light);
    font-weight: 300;
    font-size: 19.5px;
    list-style: none;
  }
  .contact-list { top: 508px; line-height: 25px; }
  .address { top: 664px; line-height: 25px; font-style: normal; letter-spacing: 0.5px; }
</style>
</head>
<body>

  <section class="card card--back" aria-label="Card back">
    <p class="back-mark">Veldmark Supplies</p>
  </section>

  <section class="card card--front" aria-label="Card front">
    <div class="front-top"></div>
    <p class="brand-line">Veldmark Supplies</p>
    <div class="brand-dot"></div>
    <p class="brand-name-mid">Veldmark Supplies</p>

    <h1 class="person-name"><span class="first">Mirela</span> <span class="last">Kostanova</span></h1>
    <p class="person-role">Co-Founder &amp; CEO</p>

    <svg class="dot-row dot-row--contact" viewBox="0 0 429 34" aria-hidden="true">
      <circle class="dot" cx="4" cy="17" r="3.3"/>
      <circle class="dot" cx="24" cy="17" r="4"/>
      <circle class="dot" cx="45" cy="17" r="5"/>
      <circle class="dot" cx="66" cy="17" r="6"/>
      <circle class="dot" cx="87" cy="17" r="7"/>
      <circle class="dot" cx="108" cy="17" r="8"/>
      <circle class="dot" cx="128" cy="17" r="9"/>
      <!-- phone -->
      <circle class="badge" cx="157" cy="17" r="15"/>
      <path class="glyph" d="M151 10 l3 0 l1.5 4 l-2 1.5 a9 9 0 0 0 4 4 l1.5 -2 l4 1.5 l0 3 a2 2 0 0 1 -2 2 a14 14 0 0 1 -12 -12 a2 2 0 0 1 2 -2z"/>
      <!-- mobile -->
      <circle class="badge" cx="196" cy="17" r="15"/>
      <rect class="glyph" x="191" y="8" width="10" height="18" rx="2"/>
      <path class="glyph" d="M195 23 h2"/>
      <!-- mail -->
      <circle class="badge" cx="234" cy="17" r="15"/>
      <rect class="glyph" x="225" y="11" width="18" height="13" rx="1"/>
      <path class="glyph" d="M225 12 l9 7 l9 -7"/>
      <!-- globe -->
      <circle class="badge" cx="272" cy="17" r="15"/>
      <circle class="glyph" cx="272" cy="17" r="8.5"/>
      <path class="glyph" d="M263.5 17 h17 M272 8.5 c-4 4 -4 13 0 17 M272 8.5 c4 4 4 13 0 17"/>
      <circle class="dot" cx="305" cy="17" r="9"/>
      <circle class="dot" cx="325" cy="17" r="8"/>
      <circle class="dot" cx="346" cy="17" r="7"/>
      <circle class="dot" cx="366" cy="17" r="6"/>
      <circle class="dot" cx="387" cy="17" r="5"/>
      <circle class="dot" cx="408" cy="17" r="4"/>
      <circle class="dot" cx="426" cy="17" r="3.3"/>
    </svg>

    <ul class="contact-list">
      <li>(555) 214-0831</li>
      <li>(555) 388-0164</li>
      <li>www.veldmarksupply.com</li>
      <li>info@veldmarksupply.com</li>
    </ul>

    <svg class="dot-row dot-row--address" viewBox="0 0 429 34" aria-hidden="true">
      <circle class="dot" cx="4" cy="17" r="3.3"/>
      <circle class="dot" cx="28" cy="17" r="4"/>
      <circle class="dot" cx="51" cy="17" r="5"/>
      <circle class="dot" cx="74" cy="17" r="6"/>
      <circle class="dot" cx="96" cy="17" r="7"/>
      <circle class="dot" cx="123" cy="17" r="8"/>
      <circle class="dot" cx="148" cy="17" r="9"/>
      <circle class="dot" cx="178" cy="17" r="10"/>
      <!-- pin -->
      <circle class="badge" cx="215" cy="17" r="15"/>
      <path class="glyph" d="M215 27 c-4 -5 -6 -8 -6 -11 a6 6 0 0 1 12 0 c0 3 -2 6 -6 11z"/>
      <circle class="glyph" cx="215" cy="16" r="2"/>
      <circle class="dot" cx="253" cy="17" r="10"/>
      <circle class="dot" cx="284" cy="17" r="9"/>
      <circle class="dot" cx="309" cy="17" r="8"/>
      <circle class="dot" cx="335" cy="17" r="7"/>
      <circle class="dot" cx="357" cy="17" r="6"/>
      <circle class="dot" cx="380" cy="17" r="5"/>
      <circle class="dot" cx="402" cy="17" r="4"/>
      <circle class="dot" cx="424" cy="17" r="3.3"/>
    </svg>

    <address class="address">48 Calloway Ridge Road,<br>Brenton, WI 53990</address>
  </section>

</body>
</html>
```